To design a brand identity that is simple and creative with 'Corvane' as the brand name, I like modern simple fonts like helvetica neue, I want to print both sides of the card, I am open to dark front and white back, but the design needs to transfer well to letter heads and email signatures, I am looking for sophisticated and elegant, but open minded about clever and off the wall, I do not do 'boring' Corvane Ventures is the mother company for a small group, specialising in Management & consulting, Software development and construction, we have a high level of integrity, we are transparent and accountable for what we do. my images are provided as a guide only, Im not expecting them to be just copied, Im looking for a creator and passionate thinker, who will put life into their work.

Target Market(s)

usually business minded people who are looking for something different in me, such as leadership, confidence and focus with thinking that is per haps a little outside the box..

Industry/Entity Type

Construction

Requirements
Must have
• clean, minmalistic
Nice to have
• custom logo
Should not have
• boring, traditional

```html
<!DOCTYPE html>
<html lang="en">
<head>
<meta charset="utf-8">
<title>Corvane — Business Card</title>
<link rel="stylesheet" href="https://fonts.googleapis.com/css2?family=Montserrat:wght@300;400;500&display=swap">
<style>
  :root {
    --backdrop: #ebebeb;
    --card: #ffffff;
    --orange: #e0622a;
    --ink: #2b2b2b;
    --grey: #6f6f6f;
    --shadow: rgba(0, 0, 0, 0.10);
  }
  * { box-sizing: border-box; margin: 0; padding: 0; }
  html, body {
    width: 1200px;
    height: 952px;
    overflow: hidden;
    background: var(--backdrop);
    font-family: "Montserrat", sans-serif;
    color: var(--ink);
  }
  .sheet {
    width: 1200px;
    height: 952px;
    display: flex;
    flex-direction: column;
    align-items: center;
    justify-content: center;
    gap: 60px;
  }
  .card {
    position: relative;
    width: 640px;
    height: 390px;
    background: var(--card);
    box-shadow: 0 8px 24px var(--shadow);
  }

  /* Front */
  .brand-name {
    position: absolute;
    left: 70px;
    top: 110px;
    font-weight: 400;
    font-size: 56px;
    letter-spacing: 10px;
    line-height: 1;
    text-transform: uppercase;
    color: var(--ink);
  }
  .services {
    position: absolute;
    left: 70px;
    top: 196px;
    font-weight: 400;
    font-size: 16px;
    letter-spacing: 0.3px;
    color: var(--ink);
  }
  .services .sep { color: var(--orange); margin: 0 6px; }
  .tagline {
    position: absolute;
    left: 70px;
    bottom: 60px;
    font-weight: 300;
    font-size: 15px;
    letter-spacing: 0.5px;
    color: var(--grey);
  }

  /* Back */
  .contact {
    position: absolute;
    left: 70px;
    top: 90px;
  }
  .contact-email {
    font-weight: 300;
    font-size: 30px;
    color: var(--orange);
    letter-spacing: 0.3px;
  }
  .contact-role {
    margin-top: 4px;
    font-weight: 400;
    font-size: 16px;
    color: var(--grey);
  }
  .contact-rule {
    margin: 14px 0 16px;
    width: 330px;
    height: 1px;
    background: linear-gradient(90deg, var(--orange), rgba(224, 98, 42, 0.15));
  }
  .contact-line {
    font-weight: 400;
    font-size: 18px;
    line-height: 1.7;
    color: var(--ink);
    letter-spacing: 0.5px;
  }
  .contact-line .label { color: var(--orange); margin-right: 10px; }
</style>
</head>
<body>
  <main class="sheet">
    <section class="card card-front" aria-label="Card front">
      <h1 class="brand-name">Corvane</h1>
      <p class="services">management<span class="sep">•</span>software<span class="sep">•</span>construction</p>
      <p class="tagline">..in the creation business.</p>
    </section>

    <section class="card card-back" aria-label="Card back">
      <div class="contact">
        <p class="contact-email">milo@corvane.ventures</p>
        <p class="contact-role">client ambassador</p>
        <div class="contact-rule"></div>
        <p class="contact-line"><span class="label">M.</span>+61 0400 512 947</p>
        <p class="contact-line"><span class="label">PO BOX</span>418 Perth 6000</p>
      </div>
    </section>
  </main>
</body>
</html>
```